New business card/stationary for a consulting company

I am looking for a clean and very professional looking business card for my consulting company as well as corresponding stationary. I am uploading our logo. I like simple and powerful for the feel. No graphics but I am open on everything else. Below is my contact information but would like the final to be in a version I can add my employees information into and print. Thank you.

Daniel Whitcombe
dan@ferncliffadvisory.com
2870 North 9th Avenue, Summit Floor, Elm Ridge, Illinois 60531
www.ferncliffadvisory.com

Industry/Entity Type

Consulting

Contact Information for Business Card

Daniel Whitcombe
dan@ferncliffadvisory.com
www.ferncliffadvisory.com

Font styles to use
Serif
Sans Serif

Requirements
Must have
• Our logo and the business card details.
Nice to have
• our website www.ferncliffadvisory.com

```html
<!DOCTYPE html>
<html lang="en">
<head>
<meta charset="utf-8">
<title>Ferncliff Advisory – Business Card</title>
<link href="https://fonts.googleapis.com/css2?family=Lato:wght@400;700&display=swap" rel="stylesheet">
<style>
  :root {
    --navy: #0b0a72;
    --navy-deep: #07065a;
    --paper: #ffffff;
    --ink: #111111;
    --backdrop: #e9e9ec;
  }
  * { margin: 0; padding: 0; box-sizing: border-box; }
  html, body {
    width: 1200px;
    height: 900px;
    overflow: hidden;
    background: var(--backdrop);
    font-family: "Lato", sans-serif;
  }
  .canvas {
    position: relative;
    width: 1200px;
    height: 900px;
  }
  .card {
    position: absolute;
    left: 250px;
    width: 700px;
    height: 400px;
    overflow: hidden;
    box-shadow: 0 6px 18px rgba(0,0,0,0.18);
  }
  .card-back {
    top: 30px;
    background: var(--navy);
    color: var(--paper);
  }
  .card-front {
    top: 470px;
    background: var(--paper);
    color: var(--ink);
  }

  /* wordmark */
  .wordmark {
    display: flex;
    align-items: center;
    gap: 14px;
    font-weight: 400;
    text-transform: uppercase;
    letter-spacing: 0.12em;
    white-space: nowrap;
  }
  .wordmark-square {
    width: 26px;
    height: 26px;
    flex: none;
  }

  /* back */
  .card-back .wordmark {
    position: absolute;
    top: 150px;
    left: 0;
    right: 0;
    justify-content: center;
    font-size: 36px;
    color: var(--paper);
  }
  .card-back .wordmark-square { background: var(--paper); }
  .card-back .website {
    position: absolute;
    top: 300px;
    left: 0;
    right: 0;
    text-align: center;
    font-size: 19px;
    letter-spacing: 0.08em;
  }

  /* front */
  .card-front .wordmark {
    position: absolute;
    top: 62px;
    left: 60px;
    font-size: 30px;
    color: var(--navy);
  }
  .card-front .wordmark-square { background: var(--navy); width: 22px; height: 22px; }
  .contact-email {
    position: absolute;
    top: 140px;
    left: 62px;
    display: flex;
    align-items: center;
    gap: 14px;
    font-size: 20px;
  }
  .contact-email svg { width: 22px; height: 16px; }
  .contact-address {
    position: absolute;
    top: 186px;
    left: 62px;
    font-style: normal;
    font-size: 20px;
    line-height: 1.3;
  }
  .holder-name {
    position: absolute;
    top: 205px;
    right: 60px;
    font-size: 32px;
    color: var(--navy);
  }
  .front-band {
    position: absolute;
    left: 0;
    bottom: 0;
    width: 700px;
    height: 400px;
  }
  .card-front .website {
    position: absolute;
    right: 50px;
    bottom: 18px;
    font-size: 21px;
    letter-spacing: 0.03em;
    color: var(--paper);
  }
</style>
</head>
<body>
<main class="canvas">

  <section class="card card-back" aria-label="Card back">
    <div class="wordmark"><span class="wordmark-square"></span>Ferncliff Advisory</div>
    <p class="website">www.ferncliffadvisory.com</p>
  </section>

  <section class="card card-front" aria-label="Card front">
    <svg class="front-band" viewBox="0 0 700 400" aria-hidden="true">
      <path d="M0,300 C220,330 470,352 700,335 L700,400 L0,400 Z" fill="var(--navy)"/>
      <path d="M110,318 C320,352 520,362 700,352" fill="none" stroke="var(--paper)" stroke-width="5"/>
    </svg>

    <div class="wordmark"><span class="wordmark-square"></span>Ferncliff Advisory</div>

    <p class="contact-email">
      <svg viewBox="0 0 22 16" aria-hidden="true">
        <rect x="0.5" y="0.5" width="21" height="15" fill="var(--navy)"/>
        <path d="M1,1 L11,9 L21,1 M1,15 L8,7 M21,15 L14,7" fill="none" stroke="var(--paper)" stroke-width="1.3"/>
      </svg>
      dan@ferncliffadvisory.com
    </p>

    <address class="contact-address">
      2870 North 9th Avenue<br>
      Summit Floor<br>
      Elm Ridge, Illinois 60531
    </address>

    <p class="holder-name">Daniel Whitcombe</p>

    <p class="website">www.ferncliffadvisory.com</p>
  </section>

</main>
</body>
</html>
```